July 2022 Industrial Manufacturer Product Expo Mexico City

We manufacture large screws and fastners for large Mining equipment, Trains, large ships, airplanes, wind turbines, and so on. We also do custom work base on the customer needs. No matter the size we can make it.
We have a Expo coming up with companies all over the world. We have to stand out we are a family own business so our customer service will be above and beyond anyone can provide. We do not have a sales force to push our products and services we provide one on one service.
Plus@!! I'm looking for anything that you designers can come up with if it was your company to put on a business card, plus i want to do a 1 or 2 sided pamphlet, and then a website. We make Speciality Bolts for large mining equipment these bolts can be 3 to 4 foot long!!! Plus fasteners, Nuts, washers, any, size, strengths, special materials, we offer more of a ono on one customer service, We are a small company, family own, but can fulfill any type of orders. We can also provide special time lines for emergency orders. "We keep the machines running we here at KRV don't believe in down time" We want to hear any slogan based on our company to stand out.
Thanks i really appreciate all your work and options that we have to pick on. Plus just a thought we could possibly want to entertain a experience Marketing internet help maybe a employment possibility. Thanks

I need 2 cards one in Spanish and English Like the steel back ground maybe send me in some bright red and blue writing Same with the Black cards Please remove the word Military The logo KRV maybe integrate a picture of a Bolt 🔩 Thank you

Still looking for I need 2 cards one in Spanish and English Like the steel back ground maybe send me in some bright red and blue writing Same with the Black cards try bright writing Please remove the word Military The logo KRV maybe integrate a picture of a Bolt 🔩 Plus will need the company to make a brochure and website next Thank you

Target Market(s)

Large Mining, Ship, Train, Green Energy, VELM, and Government equipment. Throughout the World

Industry/Entity Type

We can Custom Manufacture any type of Fastners for Mining equipment, Trains, Ships, Green energy, Governments, or military projects. wind turbines,

Contact Information for Business Card

I attached the name and contact info that's on a card, plus the Company Logo. Would like industrial looking background with Bright Colors that will stand out!! If we can insert somewhere maybe on back that we "Custom Manufacture Any Size or Quantity Fastners for Large Mining Equipment, Trains, Ships, Green Energy Equipment or Government Projects

Font styles to use
Other font styles liked:
• You Pick, has to be bold, colorful standout, Professional looking Beable to read it.

Colors

Designer to choose colors to be used in the design.

Requirements
Must have
• Need in Spanish and English TO STANDOUT FROM THE REST OF THE EXPO!! See Business card details, Rounded corners
Nice to have
• Can i see some of the darker cards with Bright Red and Blue letters I like to see the different type of card material, heavy thickness, plastic, transparent, Metal types, Bright Colors, I saw like Raised letters like on the logo.

```html
<!DOCTYPE html>
<html lang="es">
<head>
<meta charset="utf-8">
<title>KRV – Tarjetas de presentación</title>
<link href="https://fonts.googleapis.com/css2?family=Roboto+Condensed:wght@400;700&display=swap" rel="stylesheet">
<style>
  :root {
    --backdrop: #4b5249;
    --card: #1b1b1c;
    --card-edge: #141415;
    --ink-light: #f2f2f2;
    --ink-soft: #d6d6d6;
    --accent-red: #ff2a2a;
    --accent-blue: #1e90ff;
  }
  * { box-sizing: border-box; margin: 0; padding: 0; }
  html, body {
    width: 902px; height: 1200px; overflow: hidden;
    background: var(--backdrop);
    font-family: "Roboto Condensed", "Arial Narrow", sans-serif;
  }
  .sheet {
    width: 902px; height: 1200px;
    display: grid; grid-template-rows: 600px 600px;
  }
  .slot { display: flex; align-items: center; justify-content: center; }
  .card {
    position: relative;
    width: 600px; height: 343px;
    background: var(--card);
    border: 1px solid var(--card-edge);
    border-radius: 10px;
    overflow: hidden;
  }

  /* front */
  .contact { position: absolute; left: 46px; top: 150px; color: var(--ink-light); }
  .contact__name { font-weight: 700; font-size: 21px; letter-spacing: .2px; color: var(--accent-blue); }
  .contact__role { font-size: 15px; color: var(--ink-soft); margin-top: 2px; }
  .contact__rule { width: 44px; height: 3px; background: var(--accent-red); margin: 9px 0 12px; }
  .contact__list { list-style: none; font-size: 15px; color: var(--ink-light); }
  .contact__list li { display: flex; align-items: center; gap: 10px; height: 21px; }
  .contact__list svg { width: 12px; height: 12px; fill: var(--accent-red); flex: none; }

  /* back */
  .brand {
    position: absolute; inset: 0;
    display: flex; flex-direction: column; align-items: center; justify-content: center;
  }
  .brand__mark { display: flex; align-items: center; gap: 18px; }
  .brand__dot { width: 34px; height: 34px; border-radius: 50%; background: var(--accent-red); flex: none; }
  .brand__name { font-weight: 700; font-size: 128px; line-height: 1; letter-spacing: 10px; color: var(--accent-blue); }
  .brand__tagline { font-weight: 700; font-size: 17px; letter-spacing: .6px; margin-top: 6px; color: var(--accent-red); }
</style>
</head>
<body>
<main class="sheet">
  <section class="slot">
    <article class="card card--front">
      <div class="contact">
        <h1 class="contact__name">Lic. Mariela Ortega Vidal</h1>
        <p class="contact__role">Cotizaciones en</p>
        <div class="contact__rule"></div>
        <ul class="contact__list">
          <li><svg viewBox="0 0 12 12" aria-hidden="true"><path d="M2.5 0.5l2 2.5-1.2 1.4c.8 1.6 2 2.8 3.6 3.6L8.3 6.8l2.7 2-.9 2.3c-5-.4-9-4.4-9.4-9.4z"/></svg>5550142287</li>
          <li><svg viewBox="0 0 12 12" aria-hidden="true"><path d="M3 0h6a1 1 0 0 1 1 1v10a1 1 0 0 1-1 1H3a1 1 0 0 1-1-1V1a1 1 0 0 1 1-1zm.5 1.5v8h5v-8z"/></svg>5550163904</li>
          <li><svg viewBox="0 0 12 12" aria-hidden="true"><path d="M0 2h12v8H0zm1 1v.4l5 3.2 5-3.2V3z"/></svg>krv.ventas@example.com</li>
        </ul>
      </div>
    </article>
  </section>
  <section class="slot">
    <article class="card card--back">
      <div class="brand">
        <div class="brand__mark">
          <span class="brand__dot" aria-hidden="true"></span>
          <p class="brand__name">KRV</p>
        </div>
        <p class="brand__tagline">FABRICACION Y DISTRIBUCION DE TORNILLOS</p>
      </div>
    </article>
  </section>
</main>
</body>
</html>
```